Brochure for a website accessibility report

This brochure is related to a report that www.qelvantrix.org sell. The report shows the results of an automated audit of a websites accessibility. It shows details of issues found with screen shots, examples of code and provides remediation advice.

The brochure will be a pdf 8.5 inches by 11 inches. It can be anywhere from 6 to 10 pages.

The FlintVue™ name itself should be “Bree Serif” font. The fonts, styles, colors and sizes are up to you.

The images used and logo of the Office of Digital Reachworks and K7P logo are upload

We highlighted in blue page extracts from the report we sell. Do not use the blue highlight, it is merely there to show you where the specific examples of the report we sell are vs the other content in the report. The areas in blue which show the content from the actual report should be shown as an extract of the actual page of the report. You have flexibility to change the layout and the way the content look.

The red square callouts over the blue content are callouts that describe the specific page extracts. We used it as a red callout only so that you would be able to see it. You should change the specific location, look and feel of the callout to be appropriate

Target Market(s)

Marketing and Technical people

Industry/Entity Type

Information Technology

Font styles to use
Sans Serif

Colors

Designer to choose colors to be used in the design.

Requirements
Should not have
• wheelchairs, images of blind people

```html
<!DOCTYPE html>
<html lang="en">
<head>
<meta charset="utf-8">
<title>FlintVue™ Report Extract — Office of Digital Reachworks</title>
<link rel="stylesheet" href="https://fonts.googleapis.com/css2?family=Roboto:wght@300;400;500;700&family=Zilla+Slab:wght@400;500&display=swap">
<style>
  :root {
    --page-bg: #f6f3ef;
    --cream: #fdf1e2;
    --white: #ffffff;
    --heading: #4f4f4f;
    --body: #666666;
    --code-green: #2faa68;
    --link-tan: #c8b08a;
    --deep-green: #2c4b3b;
    --snippet-bg: #f8f4ee;
    --rule: #ece6dd;
  }
  * { margin: 0; padding: 0; box-sizing: border-box; }
  html, body { width: 928px; height: 1200px; overflow: hidden; background: var(--page-bg); }
  body { position: relative; font-family: "Roboto", Arial, sans-serif; color: var(--body); }

  .report-sheet {
    position: absolute; left: 54px; top: -40px; width: 823px; height: 1189px;
    background: var(--cream); border-radius: 0 0 86px 86px;
    box-shadow: 0 6px 18px rgba(0,0,0,0.06);
  }
  .abs { position: absolute; }
  .section-label { font-size: 16px; font-weight: 500; color: var(--heading); }
  .body-text { font-size: 16px; font-weight: 300; line-height: 19.5px; color: var(--body); }
  .code-line { font-family: "Zilla Slab", Georgia, serif; font-size: 15px; color: var(--code-green); white-space: nowrap; }
  .reading-link { font-size: 16.5px; color: var(--link-tan); line-height: 21px; }

  .example-card {
    position: absolute; left: 83px; top: 414px; width: 762px; height: 703px;
    background: var(--white); border-radius: 34px;
  }
  .example-divider {
    position: absolute; left: 83px; top: 766px; width: 762px; height: 3px;
    background: var(--rule); box-shadow: 0 -2px 4px rgba(0,0,0,0.04);
  }
  .example-title { font-size: 16px; color: var(--deep-green); letter-spacing: 0.2px; white-space: nowrap; }
  .example-title strong { font-weight: 700; margin-right: 10px; }

  .page-capture {
    position: absolute; left: 105px; top: 469px; width: 309px; height: 249px;
    background: linear-gradient(160deg, #f2efe9 0%, #c9b49a 45%, #8a7561 100%);
    box-shadow: 0 2px 8px rgba(0,0,0,0.18);
  }

  .callout { position: absolute; left: 468px; top: 680px; width: 299px; height: 117px; }
  .callout-text {
    position: absolute; left: 499px; top: 705px; width: 236px;
    font-size: 14.5px; line-height: 22.5px; text-transform: uppercase; text-align: justify;
    color: var(--body); font-weight: 400;
  }

  .issue-heading { font-size: 16px; font-weight: 500; color: var(--heading); text-transform: uppercase; }
  .issue-line { font-size: 15px; font-weight: 300; color: var(--body); white-space: nowrap; }
  .issue-line .hl { font-family: "Zilla Slab", Georgia, serif; color: var(--code-green); font-size: 14.5px; }
  .issue-line .tag { color: var(--code-green); }

  .snippet-box {
    position: absolute; left: 104px; top: 984px; width: 720px; height: 86px;
    background: var(--snippet-bg); box-shadow: 0 1px 5px rgba(0,0,0,0.05);
  }
  .snippet-line { font-family: "Zilla Slab", Georgia, serif; font-size: 13.5px; color: var(--code-green); white-space: nowrap; }
</style>
</head>
<body>
  <div class="report-sheet"></div>

  <div class="abs section-label" style="left:104px; top:48px;">General Remediation Advice:</div>
  <p class="abs body-text" style="left:104px; top:75px; width:730px;">When dealing with images directly contained within links with link text, don't use the same text in the image alt text as the link text.</p>

  <div class="abs section-label" style="left:104px; top:134px;">Before:</div>
  <div class="abs code-line" style="left:143px; top:159px;">&lt;a href="products.html"&gt;&lt;img src="products.gif" alt="Products page"/&gt;Products page&lt;/a&gt;</div>
  <p class="abs body-text" style="left:141px; top:182px; width:690px;">This leads to a "stutter" as screen readers will read "Products page" twice: once for the image and once for the link. Replace the alt text with "".</p>

  <div class="abs section-label" style="left:104px; top:242px;">After:</div>
  <div class="abs code-line" style="left:143px; top:268px;">&lt;a href="products.html"&gt;&lt;img src="icon.gif" alt="" /&gt;Products page&lt;/a&gt;</div>

  <div class="abs section-label" style="left:104px; top:306px;">Suggested Reading:</div>
  <div class="abs reading-link" style="left:147px; top:326px;">Compatible</div>
  <div class="abs reading-link" style="left:147px; top:347px;">Link Purpose (In Context)</div>

  <div class="example-card"></div>
  <div class="example-divider"></div>

  <div class="abs example-title" style="left:103px; top:433px;"><strong>EXAMPLE 1 OF 7:</strong>HTTPS://WWW.VELMORA-UNION.ORG/SOCIAL/INCLUSION-ES/</div>

  <div class="page-capture" role="img" aria-label="Screenshot of the audited web page showing a news layout with a large feature photo, side stories and three topic tiles"></div>

  <svg class="callout" viewBox="0 0 299 150" width="299" height="150" style="height:150px;">
    <path d="M20 0 H279 A20 20 0 0 1 299 20 V97 A20 20 0 0 1 279 117 H62 L47 144 L38 117 H20 A20 20 0 0 1 0 97 V20 A20 20 0 0 1 20 0 Z" fill="#fdf0de"/>
  </svg>
  <div class="callout-text">The specific issue discovered provides detail needed to understand the issue</div>

  <div class="abs issue-heading" style="left:104px; top:818px;">Specific Issues:</div>
  <div class="abs issue-line" style="left:104px; top:841px;">Image links should not duplicate link-text with the 'ALT' attribute.</div>
  <div class="abs issue-line" style="left:104px; top:864px;">Found link text ' <span class="hl">MÁS INFORMACIÓN</span> ' within ALT of <span class="tag">&lt;IMG&gt; Tag</span></div>
  <div class="abs issue-line" style="left:104px; top:886px;"><span class="tag">src='http://www.velmora-union.org/social/inclusion-fr/wp-content/uploads/sites&nbsp;/28/2015/10/ico_en.gif'.</span></div>

  <div class="abs issue-heading" style="left:104px; top:950px;">Code Snippet</div>
  <div class="snippet-box"></div>
  <div class="abs snippet-line" style="left:124px; top:999px;">&lt;IMG STYLE="VERTICAL-ALIGN: BASELINE" SRC="HTTP://WWW.VELMORA-UNION.ORG/SOCIAL/</div>
  <div class="abs snippet-line" style="left:124px; top:1018px;">INCLUSION-FR /WPCONTENT/UPLOADS/SITES /28/2015/10/ICO_EN.GIF" ALT="M&amp;#193;S</div>
  <div class="abs snippet-line" style="left:124px; top:1037px;">INFORMACI&amp;#211;N"&gt;</div>
</body>
</html>
```